Stationary - Based On Previous Design

Basic stationary with a header and footer

Target Market(s)

Friends, Colleagues, More friendly than professional

Industry/Entity Type

legal/personal

Colors
00AB8E
00BBA5
67D7C9
C6EFE9
E9F9F6

Requirements
Must have
• Green & White
Nice to have
• I like the "G" on the business card and was thinking that would be for both G's in "PellaNote"
Should not have
• other colors

```html
<!DOCTYPE html>
<html lang="en">
<head>
<meta charset="utf-8">
<title>PellaNote Stationery</title>
<link href="https://fonts.googleapis.com/css2?family=Arimo:wght@400;700&family=Montserrat:wght@400;500;700&display=swap" rel="stylesheet">
<style>
  :root{
    --green:#0f4a22;
    --green-mid:#1e4a2a;
    --ink:#07140d;
    --gray:#3a3a3a;
    --text:#2b2b2b;
    --muted:#8a8a8a;
    --paper:#ffffff;
    --bg:#8fb3d9;
  }
  *{margin:0;padding:0;box-sizing:border-box}
  html,body{width:936px;height:1200px;overflow:hidden}
  body{background:var(--bg);position:relative;font-family:"Arimo",Arial,sans-serif;color:var(--text)}
  .piece{position:absolute;background:var(--paper);box-shadow:2px 3px 6px rgba(0,0,0,.25);overflow:hidden}
  .brand{font-family:"Montserrat",Arial,sans-serif;font-weight:700;color:var(--green);letter-spacing:-.3px;line-height:1;white-space:nowrap}
  .stripe{position:absolute;left:0;right:0;bottom:0;display:flex;height:7px}
  .stripe .band{flex:1;background:var(--green);clip-path:polygon(0 0,100% 0,calc(100% - 7px) 100%,0 100%)}
  .stripe .tail{width:27%;background:var(--gray);margin-left:-3px;clip-path:polygon(10px 0,100% 0,100% 100%,3px 100%)}
  .icon{width:8px;height:8px;vertical-align:-1px;margin-right:4px;fill:var(--green)}

  /* business card front */
  .card-front{left:37px;top:44px;width:368px;height:211px}
  .card-front .brand{position:absolute;right:24px;top:42px;font-size:34px}
  .card-front .name{position:absolute;left:23px;top:118px;font-size:12.5px;font-weight:700;color:var(--green)}
  .card-front .role{position:absolute;left:23px;top:133px;font-size:9px}
  .card-front .rule{position:absolute;left:23px;right:24px;top:148px;border-top:1px solid #999}
  .card-front .contact{position:absolute;left:23px;top:157px;font-size:8.6px;line-height:13px}
  .card-front .address{position:absolute;right:24px;top:159px;font-size:8.6px;line-height:12px;text-align:right}

  /* monarch sheet */
  .sheet{left:439px;top:44px;width:477px;height:211px}
  .sheet .brand{position:absolute;left:13px;top:20px;font-size:22px}
  .sheet .address{position:absolute;left:13px;top:57px;font-size:6.6px;line-height:8px}

  /* card back */
  .card-back{left:37px;top:282px;width:368px;height:211px;background:var(--ink)}
  .card-back .brand{position:absolute;left:22px;top:126px;font-size:38px;color:#fff}

  /* envelope */
  .envelope{left:439px;top:282px;width:477px;height:208px}
  .envelope .flap{position:absolute;left:0;top:0;width:100%;height:64px}
  .envelope .brand{position:absolute;left:0;right:0;top:18px;text-align:center;font-size:20px}

  /* letterhead */
  .letter{left:30px;top:526px;width:434px;height:614px;background:linear-gradient(90deg,#fff 60%,#f3f3f3)}
  .letter .brand{position:absolute;left:31px;top:32px;font-size:24px}
  .letter .head-info{position:absolute;left:281px;top:20px;font-size:6.8px;line-height:8.6px}
  .letter .head-info .gap{height:8px}
  .letter .rule{position:absolute;left:31px;right:32px;top:70px;border-top:1px solid #333}
  .letter .to{position:absolute;left:44px;top:137px;font-family:"Montserrat",sans-serif;font-size:6.4px;line-height:9.4px;color:var(--muted)}
  .letter .to .label{color:var(--text);letter-spacing:1px}
  .letter .to .who{color:var(--green);font-size:7px}
  .letter .date{position:absolute;right:44px;top:137px;font-family:"Montserrat",sans-serif;font-size:6px;color:var(--muted)}
  .letter .body{position:absolute;left:44px;right:44px;top:221px;font-family:"Montserrat",sans-serif;font-size:5.9px;line-height:7.8px;color:var(--muted);text-align:justify}
  .letter .body p{margin-bottom:7px}
  .letter .signature{position:absolute;left:44px;top:432px;width:76px;height:16px;background:linear-gradient(90deg,#e4e4e4,#f2f2f2)}
  .letter .signer{position:absolute;left:44px;top:457px;font-family:"Montserrat",sans-serif;font-size:6.4px;line-height:8.5px}
  .letter .signer span{display:block;color:var(--muted);font-size:5.6px}

  /* folder closed */
  .folder{left:495px;top:526px;width:413px;height:292px;display:flex}
  .folder .cover{width:205px;background:var(--ink)}
  .folder .inner{flex:1;position:relative;background:linear-gradient(90deg,#fff,#eee)}
  .folder .brand{position:absolute;left:14px;top:15px;font-size:11px}
  .mini-info{position:absolute;font-size:3.4px;line-height:4.4px}
  .folder .mini-info{right:14px;top:11px}
  .mini-rule{position:absolute;border-top:.6px solid #555}
  .folder .mini-rule{left:14px;right:14px;top:34px}
  .folder .stripe{left:205px;height:4px}

  /* folder open */
  .folder-open{left:495px;top:849px;width:413px;height:292px;background:linear-gradient(90deg,#fff 0%,#e9e9e9 48%,#bdbdbd 50%,#f3f3f3 52%,#fff)}
  .insert{position:absolute;left:216px;top:11px;width:184px;height:186px;background:#fafafa}
  .insert .brand{position:absolute;left:14px;top:20px;font-size:9px}
  .insert .mini-info{right:12px;top:18px}
  .insert .mini-rule{left:14px;right:12px;top:37px}
  .insert .mini-body{position:absolute;left:20px;right:14px;top:60px;font-family:"Montserrat",sans-serif;font-size:3.4px;line-height:4.6px;color:var(--muted)}
  .insert .mini-body b{color:var(--green);font-weight:500}
  .pockets{position:absolute;left:0;bottom:0;width:413px;height:106px}
</style>
</head>
<body>

<section class="piece card-front" aria-label="Business card front">
  <div class="brand">PellaNote</div>
  <div class="name">Dana Whitfield</div>
  <div class="role">President, Chief Legal Counsel</div>
  <div class="rule"></div>
  <div class="contact">
    <div><svg class="icon" viewBox="0 0 10 10"><path d="M2 0.5l2 2-1 1.2c.6 1.3 1.6 2.3 2.9 2.9l1.2-1 2 2-1.4 1.9C4.5 9.3.7 5.5.3 2z"/></svg>555.014.2210</div>
    <div><svg class="icon" viewBox="0 0 10 10"><path d="M0 1.5h10v7H0z M0 1.5l5 4 5-4" stroke="#fff" stroke-width=".8"/></svg>dana@pellanote.com</div>
  </div>
  <div class="address">40 Harbor Lane, Suite 300<br>Lakeview, IL 60000</div>
  <div class="stripe"><div class="band"></div><div class="tail"></div></div>
</section>

<section class="piece sheet" aria-label="Monarch sheet">
  <div class="brand">PellaNote</div>
  <div class="address">40 Harbor Lane, Suite 300<br>Lakeview, IL 60000</div>
  <div class="stripe"><div class="band"></div><div class="tail"></div></div>
</section>

<section class="piece card-back" aria-label="Business card back">
  <div class="brand">PellaNote</div>
</section>

<section class="piece envelope" aria-label="Envelope back">
  <svg class="flap" viewBox="0 0 477 64" preserveAspectRatio="none">
    <path d="M0 0 L12 48 Q16 58 30 58 L447 58 Q461 58 465 48 L477 0" fill="#fff" stroke="#ddd" stroke-width="1"/>
  </svg>
  <div class="brand">PellaNote</div>
</section>

<section class="piece letter" aria-label="Letterhead">
  <div class="brand">PellaNote</div>
  <div class="head-info">
    40 Harbor Lane, Suite 300<br>Lakeview, IL 60000
    <div class="gap"></div>
    <svg class="icon" viewBox="0 0 10 10"><path d="M2 0.5l2 2-1 1.2c.6 1.3 1.6 2.3 2.9 2.9l1.2-1 2 2-1.4 1.9C4.5 9.3.7 5.5.3 2z"/></svg>555.014.2210<br>
    <svg class="icon" viewBox="0 0 10 10"><path d="M0 1.5h10v7H0z M0 1.5l5 4 5-4" stroke="#fff" stroke-width=".8"/></svg>dana@pellanote.com
  </div>
  <div class="rule"></div>
  <div class="to">
    <div class="label">TO</div>
    <div class="who">Lena Marsh</div>
    Human Resources<br>Brightfield Co.<br>12 Orchard Row, Fairhaven<br>00412 USA
  </div>
  <div class="date">Friday, 01/01/2018</div>
  <div class="body">
    <p>Lorem ipsum dolor sit amet, consectetuer adipiscing elit, sed diam nonummy nibh euismod tincidunt ut laoreet dolore magna aliquam erat volutpat. Ut wisi enim ad minim veniam, quis nostrud exerci tation ullamcorper suscipit lobortis nisl ut aliquip ex ea commodo consequat. Duis autem vel eum iriure dolor in hendrerit in vulputate velit esse molestie consequat, vel illum dolore eu feugiat nulla facilisis at vero eros et accumsan et iusto odio dignissim qui blandit praesent luptatum zzril delenit augue duis dolore te feugait nulla facilisi.</p>
    <p>Nam liber tempor cum soluta nobis eleifend option congue nihil imperdiet doming id quod mazim placerat facer possim assum. Typi non habent claritatem insitam.</p>
    <p>Est usus legentis in iis qui facit eorum claritatem.</p>
    <p>Investigationes demonstraverunt lectores legere me lius quod ii legunt saepius. Claritas est etiam processus dynamicus, qui sequitur mutationem consuetudium lectorum. Mirum est notare quam littera gothica, quam nunc putamus parum claram, anteposuerit litterarum formas humanitatis per seacula quarta decima et quinta decima. Eodem modo typi, qui nunc nobis videntur parum clari, fiant sollemnes in futurum.</p>
    <p>Consectetuer adipiscing elit, sed diam nonummy nibh euismod tincidunt ut laoreet dolore magna aliquam erat volutpat. Ut wisi enim ad minim veniam, quis nostrud exerci tation ullamcorper suscipit lobortis nisl ut aliquip ex ea commodo consequat. Duis autem vel eum iriure dolor in hendrerit in vulputate velit esse molestie consequat, vel illum dolore eu feugiat nulla facilisis at vero eros et accumsan et iusto odio dignissim qui blandit praesent luptatum zzril delenit augue duis dolore te feugait nulla facilisi.</p>
    <p>Nam liber tempor cum soluta nobis eleifend option congue nihil imperdiet.</p>
  </div>
  <div class="signature" role="img" aria-label="Handwritten signature"></div>
  <div class="signer">Owen Tate<span>Managing Director</span></div>
  <div class="stripe"><div class="band"></div><div class="tail"></div></div>
</section>

<section class="piece folder" aria-label="Presentation folder, outside">
  <div class="cover"></div>
  <div class="inner">
    <div class="brand">PellaNote</div>
    <div class="mini-info">40 Harbor Lane, Suite 300<br>Lakeview, IL 60000<br><br>555.014.2210<br>dana@pellanote.com</div>
    <div class="mini-rule"></div>
  </div>
  <div class="stripe"><div class="band"></div><div class="tail"></div></div>
</section>

<section class="piece folder-open" aria-label="Presentation folder, inside">
  <div class="insert">
    <div class="brand">PellaNote</div>
    <div class="mini-info">40 Harbor Lane, Suite 300<br>Lakeview, IL 60000<br>555.014.2210<br>dana@pellanote.com</div>
    <div class="mini-rule"></div>
    <div class="mini-body">
      TO<br><b>Lena Marsh</b><br>Human Resources<br>Brightfield Co.<br><br>
      Thank you for meeting with us this week. We enjoyed the conversation and look forward to working together on the matters we discussed soon.
    </div>
  </div>
  <svg class="pockets" viewBox="0 0 413 106" preserveAspectRatio="none">
    <path d="M0 0 H185 Q191 0 192 8 L205 106 H0 Z" fill="var(--green-mid)"/>
    <path d="M413 0 H221 Q215 0 214 8 L205 106 H413 Z" fill="var(--green-mid)"/>
  </svg>
</section>

</body>
</html>
```